Wed site for biomedical device startup

We need a generic website for a medical device startup. I will provide examples below of websites from other companies that can serve as models for what we are looking for. The startup is for a device that can non invasively measure blood flow in the brain using light. The application is to detect the type of stroke someone is having before they get to the hospital so treatment can be started right away. This saves patients upto hours of delayed treatment. Patients will be able to recover from stroke much better and faster as a result. I have attached an AI generated illustration of what the device will ultimately look like for reference.

https://www.372clinicaltech.com
https://vextalune.com

Target Market(s)

Biomedical, medical device, investors of biomedical device startups

Industry/Entity Type

Biomedical

Coding

Coded - Design and coding required

Number of Pages Required

4 page

Requirements
Must have
• same section and section headings as example websites listed above
Nice to have
• similar to example websites listed above. Prefer a darker website over a lighter one. Perhaps dark blues to go with logo colors. A moving background image element at top of landing page could be cool. Something indicative of heartbeat, or neurons, or blood flow.

```html
<!DOCTYPE html>
<html lang="en">
<head>
<meta charset="utf-8">
<title>Nevaro – Smart Blood Loss Monitoring</title>
<link rel="stylesheet" href="https://fonts.googleapis.com/css2?family=Montserrat:wght@400;500;600;700&display=swap">
<style>
  :root {
    --ink: #000000;
    --navy: #06054a;
    --navy-deep: #05043d;
    --white: #ffffff;
    --violet: #9a3ee0;
    --violet-deep: #6a2bd6;
    --blue: #3f6fe0;
    --cyan: #29b6e8;
    --hero-a: #0b1a55;
    --hero-b: #1e3d8a;
    --hero-c: #3a1d6e;
  }
  * { margin: 0; padding: 0; box-sizing: border-box; }
  html, body { width: 1200px; height: 3369px; overflow: hidden; background: var(--ink); }
  body { position: relative; font-family: "Montserrat", sans-serif; color: var(--white); }
  .abs { position: absolute; }

  /* hero */
  .hero {
    position: absolute; left: 0; top: 0; width: 1200px; height: 633px;
    background:
      radial-gradient(circle at 85% 18%, rgba(80,200,210,.45), transparent 22%),
      radial-gradient(circle at 12% 30%, rgba(90,120,230,.45), transparent 28%),
      radial-gradient(circle at 50% 75%, rgba(150,60,170,.45), transparent 35%),
      linear-gradient(160deg, var(--hero-a), var(--hero-b) 45%, var(--hero-c));
  }
  .brand { display: flex; align-items: center; gap: 10px; font-weight: 500; letter-spacing: 2px; }
  .brand-dot { border-radius: 50%; background: linear-gradient(135deg, var(--cyan), var(--violet)); }
  .nav-brand { left: 112px; top: 38px; font-size: 32px; }
  .nav-brand .brand-dot { width: 46px; height: 46px; }
  .nav-menu { left: 658px; top: 51px; display: flex; gap: 20px; font-size: 15px; font-weight: 500; list-style: none; }
  .nav-menu .current { font-weight: 700; }
  .hero-title { left: 0; width: 1200px; top: 170px; text-align: center; font-size: 43px; font-weight: 700; line-height: 62px; }
  .hero-text { left: 0; width: 1200px; top: 303px; text-align: center; font-size: 15.5px; line-height: 27px; }
  .btn {
    display: flex; align-items: center; justify-content: center;
    border-radius: 28px; font-size: 16px; font-weight: 500;
    background: linear-gradient(180deg, var(--violet), var(--violet-deep) 60%, var(--blue));
  }
  .hero-btn { left: 490px; top: 390px; width: 222px; height: 53px; }

  /* technology */
  .tech-panel { left: 114px; top: 537px; width: 977px; height: 860px; background: var(--navy); border-radius: 30px; }
  .eyebrow { left: 172px; top: 597px; font-size: 19px; font-weight: 600; }
  .section-heading { font-size: 32px; font-weight: 600; }
  .tech-heading { left: 172px; top: 632px; }
  .feature-icon {
    width: 68px; height: 68px; border-radius: 50%;
    background: linear-gradient(160deg, var(--violet), var(--blue));
    display: flex; align-items: center; justify-content: center;
  }
  .feature-title { font-size: 19px; font-weight: 600; }
  .feature-text { font-size: 15px; line-height: 22px; width: 690px; }
  .video {
    left: 172px; top: 1048px; width: 860px; height: 491px; border-radius: 30px;
    background: linear-gradient(135deg, #8f5cd8, #6a4fc0 45%, #7d4fd0 70%, #a16fe0);
  }
  .play { left: 575px; top: 1266px; }

  /* partners */
  .centered { left: 0; width: 1200px; text-align: center; }
  .partner-card {
    width: 183px; height: 147px; border-radius: 6px; padding: 2px;
    background: linear-gradient(160deg, var(--violet), var(--cyan));
  }
  .partner-card .inner {
    width: 100%; height: 100%; border-radius: 5px; background: var(--ink);
    display: flex; align-items: center; justify-content: center;
  }
  .partner-card .badge { width: 70px; height: 70px; border-radius: 50%; background: var(--white); }
  .partner-card.featured .inner { background: linear-gradient(180deg, #b26ae6, var(--violet-deep) 50%, var(--cyan)); }
  .more-btn { left: 489px; top: 2173px; width: 222px; height: 52px; }

  /* subscribe */
  .team-photo { left: 112px; top: 2480px; width: 440px; height: 484px; background: linear-gradient(160deg, #a046e0, #d8c6ee 55%, #c7a4ec); }
  .subscribe-heading { left: 598px; top: 2482px; font-size: 26px; font-weight: 500; }
  .field {
    left: 598px; width: 414px; height: 55px; border-radius: 6px; padding: 2px;
    background: linear-gradient(90deg, var(--violet), var(--cyan));
  }
  .field .inner {
    width: 100%; height: 100%; border-radius: 5px; background: var(--ink);
    padding-left: 15px; display: flex; align-items: center; font-size: 15px;
  }
  .subscribe-btn { left: 598px; top: 2915px; width: 174px; height: 53px; font-size: 18px; }

  /* footer */
  .footer { left: 0; top: 3096px; width: 1200px; height: 273px; background: var(--navy-deep); }
  .footer-brand { left: 206px; top: 3151px; font-size: 44px; }
  .footer-brand .brand-dot { width: 64px; height: 64px; }
  .social { top: 3161px; width: 44px; height: 44px; border-radius: 50%; background: var(--white); }
  .footer-menu { left: 0; width: 1200px; top: 3266px; display: flex; justify-content: center; gap: 21px; font-size: 16px; list-style: none; }
  .footer-rule { left: 0; top: 3326px; width: 1200px; height: 1px; background: rgba(255,255,255,.35); }
  .copyright { top: 3340px; font-size: 13.5px; }
</style>
</head>
<body>

<header class="hero" role="img" aria-label="Glowing blue and violet neuron network background"></header>
<div class="abs brand nav-brand"><span class="brand-dot"></span>NEVARO</div>
<ul class="abs nav-menu">
  <li class="current">HOME</li><li>ABOUT</li><li>TECHNOLOGY</li><li>PRESS</li><li>CONTACT</li>
</ul>
<h1 class="abs hero-title">SMART BLOOD<br>LOSS MONITORING</h1>
<p class="abs hero-text">Advanced wearable technology that continuously monitors blood loss and vital<br>signs, providing real-time data to caregivers and patients for better health</p>
<div class="abs btn hero-btn">CONTACT WITH US</div>

<section>
  <div class="abs tech-panel"></div>
  <p class="abs eyebrow">Advanced Technology</p>
  <h2 class="abs section-heading tech-heading">Innovative Blood Loss Monitoring</h2>

  <div class="abs feature-icon" style="left:214px;top:712px">
    <svg width="34" height="34" viewBox="0 0 34 34" fill="none" stroke="#fff" stroke-width="2"><rect x="13" y="3" width="16" height="28" rx="3"/><rect x="4" y="10" width="7" height="16" rx="3"/><path d="M17 10h8M17 15h8M17 20h5"/></svg>
  </div>
  <h3 class="abs feature-title" style="left:309px;top:714px">Portable Monitoring</h3>
  <p class="abs feature-text" style="left:309px;top:748px">Compact, wearable devices that provide continuous blood loss monitoring anywhere, anytime.</p>

  <div class="abs feature-icon" style="left:214px;top:820px">
    <svg width="34" height="34" viewBox="0 0 34 34" fill="none" stroke="#fff" stroke-width="2"><path d="M28 14A12 12 0 1 0 16 29"/><path d="M16 9v8l5 3"/><circle cx="25" cy="24" r="6"/><path d="M22 24l2 2 4-4"/></svg>
  </div>
  <h3 class="abs feature-title" style="left:309px;top:822px">Real-time Alerts</h3>
  <p class="abs feature-text" style="left:309px;top:857px">Instant notifications to caregivers when critical thresholds are reached.</p>

  <div class="abs feature-icon" style="left:214px;top:909px">
    <svg width="34" height="34" viewBox="0 0 34 34" fill="none" stroke="#fff" stroke-width="2"><circle cx="22" cy="10" r="5"/><path d="M13 31c0-6 4-10 9-10s9 4 9 10"/><path d="M6 4v7a4 4 0 0 0 8 0V4"/><path d="M10 15v8"/></svg>
  </div>
  <h3 class="abs feature-title" style="left:309px;top:912px">Patient-Centered</h3>
  <p class="abs feature-text" style="left:309px;top:946px">Easy-to-use interface designed for both patients and healthcare providers.</p>

  <div class="abs video" role="img" aria-label="Video still of two scientists reviewing data on a tablet in a laboratory"></div>
  <svg class="abs play" width="56" height="56" viewBox="0 0 56 56" fill="none"><circle cx="28" cy="28" r="25" stroke="#fff" stroke-width="3"/><path d="M23 18l14 10-14 10z" fill="#fff"/></svg>
</section>

<section>
  <h2 class="abs section-heading centered" style="top:1634px">Partners and Collaborators</h2>
  <p class="abs centered" style="top:1689px;font-size:15.5px">Working together with leading institutions to advance medical technology</p>

  <div class="abs partner-card" style="left:161px;top:1771px"><div class="inner"><span class="badge"></span></div></div>
  <div class="abs partner-card featured" style="left:393px;top:1768px"><div class="inner"><span class="badge"></span></div></div>
  <div class="abs partner-card" style="left:625px;top:1768px"><div class="inner"><span class="badge"></span></div></div>
  <div class="abs partner-card" style="left:857px;top:1771px"><div class="inner"><span class="badge"></span></div></div>
  <div class="abs partner-card" style="left:161px;top:1964px"><div class="inner"><span class="badge"></span></div></div>
  <div class="abs partner-card" style="left:393px;top:1961px"><div class="inner"><span class="badge"></span></div></div>
  <div class="abs partner-card" style="left:625px;top:1961px"><div class="inner"><span class="badge"></span></div></div>
  <div class="abs partner-card" style="left:857px;top:1964px"><div class="inner"><span class="badge"></span></div></div>

  <div class="abs btn more-btn">VIEW MORE</div>
</section>

<section>
  <h2 class="abs section-heading centered" style="top:2308px">Stay Connected</h2>
  <p class="abs centered" style="top:2372px;font-size:15.5px;line-height:26px">Join our community to receive updates about our latest developments and<br>research in blood loss monitoring technology.</p>

  <div class="abs team-photo" role="img" aria-label="Photo of a smiling team of four healthcare professionals"></div>

  <h3 class="abs subscribe-heading">Subscribe Now</h3>
  <div class="abs field" style="top:2555px"><div class="inner">Email Address *</div></div>
  <div class="abs field" style="top:2644px"><div class="inner">First Name *</div></div>
  <div class="abs field" style="top:2733px"><div class="inner">Last Name</div></div>
  <div class="abs field" style="top:2821px"><div class="inner">Company</div></div>
  <div class="abs btn subscribe-btn">Subscribe</div>
</section>

<footer>
  <div class="abs footer"></div>
  <div class="abs brand footer-brand"><span class="brand-dot"></span>NEVARO</div>
  <span class="abs social" style="left:734px"></span>
  <span class="abs social" style="left:787px"></span>
  <span class="abs social" style="left:840px"></span>
  <span class="abs social" style="left:893px"></span>
  <span class="abs social" style="left:946px"></span>
  <ul class="abs footer-menu">
    <li>HOME</li><li>ABOUT</li><li>TECHNOLOGY</li><li>PRESS</li><li>CONTACT</li><li>TERMS &amp; CONDITIONS</li><li>PRIVACY POLICY</li>
  </ul>
  <div class="abs footer-rule"></div>
  <p class="abs centered copyright">2025 Biomedical Startup. All rights reserved.</p>
</footer>

</body>
</html>
```